Business cards for Norwegian software consultancy business

We are in need of business cards for our Norwegian consultancy company.
“Valto Brindex AS” specializes in software development, architecture and agile methodology, providing mostly on-site services at customers.
The cards should reflect a certain level of business professionalism with an elegant touch, while paying tribute to our modern and technological heritage. Our logo should be featured, as well as room for basic information about the cardholder and legal information of the company (company name, address and VAT number).
We would like our cards to reflect that we are a modern consulting company. It should present a professional image that people will remember. The texture and color pallette should reflect our professionalism and reliability, so we prefer a light color pallette with colors such as gray, white, blue and black. The number of colors used should however not be overwhelming, with the text being distinct and readable.
We are open to untraditional layouts and playful designs as long as they communicate the intent stated above.
You could also take a look at our website http://www.brindex.no for input on our visual profile.
Our logo is attached in the form of vectors and rasterized PNG. Please comment if you would like the black-white and/or inverted versions as well.
Industry/Entity Type
Architecture
Contact Information for Business Card
Company information:
Valto Brindex AS
Kvernlia 14, 3170 Sem
482 71 519
info@brindex.no
www.brindex.no
Employee information:
Full name
Title
Email
Phone
Font styles to use
Look and feel

```html
<!DOCTYPE html>
<html lang="en">
<head>
<meta charset="utf-8">
<title>Valto Brindex AS – Business Cards</title>
<link rel="stylesheet" href="https://fonts.googleapis.com/css2?family=Lato:wght@400;700&display=swap">
<style>
  :root {
    --stage: #2a2a2a;
    --paper: #ffffff;
    --paper-shade: #e4e4e4;
    --ink: #1b1b1b;
    --night: #0d0d0d;
    --brand-blue: #4a8fc9;
    --brand-blue-deep: #2f6ea6;
    --muted: #bfbfbf;
    --ghost: #262626;
  }
  * { box-sizing: border-box; margin: 0; padding: 0; }
  html, body { width: 1200px; height: 873px; overflow: hidden; }
  body {
    background: var(--stage);
    font-family: "Lato", Arial, sans-serif;
    position: relative;
  }
  .card {
    position: absolute;
    width: 540px;
    height: 310px;
    border-radius: 22px;
    overflow: hidden;
    box-shadow: 0 14px 36px rgba(0,0,0,.55);
  }
  .card--front {
    left: 40px; top: 282px;
    background: linear-gradient(160deg, var(--paper) 0%, var(--paper) 45%, var(--paper-shade) 100%);
    display: flex; align-items: center; justify-content: center;
  }
  .card--back {
    left: 620px; top: 282px;
    background: var(--paper);
  }
  .brand {
    display: flex; align-items: center; gap: 14px;
    color: var(--ink);
    font-weight: 400;
    letter-spacing: 3px;
    text-transform: uppercase;
  }
  .brand__square {
    width: 22px; height: 22px;
    background: var(--brand-blue);
  }
  .brand__name { font-size: 34px; }
  .card--back .brand {
    position: absolute; left: 0; right: 0; top: 40px;
    justify-content: center;
  }
  .card--back .brand__name { font-size: 30px; }
  .card__shapes { position: absolute; inset: 0; }
  .holder {
    position: absolute; left: 130px; width: 290px; top: 147px;
    text-align: center; color: var(--paper);
  }
  .holder__name { font-weight: 700; font-size: 19px; line-height: 24px; }
  .holder__title { font-size: 12.5px; line-height: 16px; }
  .contact {
    position: absolute; left: 30px; top: 208px;
    color: var(--paper); font-size: 12.5px; line-height: 17px;
  }
  .contact__company { text-transform: uppercase; }
  .contact__address { color: var(--brand-blue); font-weight: 700; margin-bottom: 6px; }
  .contact__list { list-style: none; }
  .contact__item { display: flex; align-items: center; gap: 12px; line-height: 19px; }
  .contact__icon { width: 12px; height: 12px; flex: none; }
</style>
</head>
<body>

  <section class="card card--front" aria-label="Card front">
    <div class="brand">
      <span class="brand__square"></span>
      <span class="brand__name">Valto Brindex</span>
    </div>
  </section>

  <section class="card card--back" aria-label="Card back">
    <svg class="card__shapes" viewBox="0 0 540 310" width="540" height="310" aria-hidden="true">
      <polygon points="0,196 540,118 540,310 0,310" fill="var(--night)"/>
      <polygon points="0,190 540,112 540,120 0,198" fill="var(--brand-blue-deep)"/>
      <polygon points="150,142 400,142 432,196 118,196" fill="var(--brand-blue)"/>
      <polygon points="118,196 150,142 135,196" fill="var(--brand-blue-deep)"/>
      <polygon points="432,196 400,142 415,196" fill="var(--brand-blue-deep)"/>
      <rect x="402" y="150" width="110" height="110" fill="none" stroke="var(--ghost)" stroke-width="14"/>
    </svg>

    <div class="brand">
      <span class="brand__square"></span>
      <span class="brand__name">Valto Brindex</span>
    </div>

    <div class="holder">
      <p class="holder__name">Henrik Aasvold</p>
      <p class="holder__title">Owner / Founder</p>
    </div>

    <div class="contact">
      <p class="contact__company">Valto Brindex AS</p>
      <p class="contact__address">Kvernlia 14, 3170 Sem, Norway</p>
      <ul class="contact__list">
        <li class="contact__item">
          <svg class="contact__icon" viewBox="0 0 12 12" aria-hidden="true"><rect x="3" y="0.5" width="6" height="11" rx="1" fill="none" stroke="var(--brand-blue)" stroke-width="1.2"/></svg>
          <span>+47 482 71 519</span>
        </li>
        <li class="contact__item">
          <svg class="contact__icon" viewBox="0 0 12 12" aria-hidden="true"><rect x="0.5" y="2" width="11" height="8" fill="var(--brand-blue)"/><polyline points="0.5,2 6,6.5 11.5,2" fill="none" stroke="var(--night)" stroke-width="1"/></svg>
          <span>info@brindex.no</span>
        </li>
        <li class="contact__item">
          <svg class="contact__icon" viewBox="0 0 12 12" aria-hidden="true"><path d="M5 7 L7 5 M4 6 L2 8 a1.5 1.5 0 0 0 2 2 L6 8 M8 6 L10 4 a1.5 1.5 0 0 0 -2 -2 L6 4" fill="none" stroke="var(--brand-blue)" stroke-width="1.3"/></svg>
          <span>www.brindex.no</span>
        </li>
      </ul>
    </div>
  </section>

</body>
</html>
```